Business card design Needed for new logo / Construction business, home extensions and new builds

We need a business card design using our new logo files which i will attach to this project :)

We are a small construction business specialising in home extensions, new builds and property development. We are very ambitious and would appreciate professional and elegant designs for our new business card.

Very serious about using the services on MakerQuarry and recently acquired our new logo from here :)

Please get involved, i will feedback when i can as i am very busy but can respond daily, thanks

Target Market(s)

People that want to build onto their houses, new building developments or adding too their existing property

Industry/Entity Type

Construction

Contact Information for Business Card

Renwick Tolliver Construction, Lionel Ashby (Managing Director), Tel 07822254961, email - info@renwick-tolliver, www.renwick-tolliver.co.uk

Colors

Designer to choose colors to be used in the design.

Requirements
Must have
• I like a deep grey on the back please. A lot of you have provided black from and back, try mixing things up a little. The black looks cool 😎 Thanks

```html
<!DOCTYPE html>
<html lang="en">
<head>
<meta charset="utf-8">
<title>Renwick Tolliver Construction – Business Card</title>
<link href="https://fonts.googleapis.com/css2?family=Cinzel:wght@500;600&family=Tinos:wght@400&display=swap" rel="stylesheet">
<style>
  :root{
    --stage:#48484b;
    --card:#161617;
    --card-back:#2c2d30;
    --card-back-light:#35363a;
    --card-back-dark:#242528;
    --gold:#d4a12a;
    --gold-light:#f1cd63;
    --gold-dark:#a7740f;
    --silver:#e4e4e4;
    --text:#dcdcdc;
    --rule:#3a3a3c;
  }
  *{margin:0;padding:0;box-sizing:border-box}
  html,body{width:1200px;height:689px;overflow:hidden;background:var(--stage)}
  .stage{position:relative;width:1200px;height:689px}
  .card{position:absolute;top:190px;width:540px;height:309px;border-radius:16px;overflow:hidden}
  .card--back{left:40px;background:var(--card-back)}
  .card--front{left:620px;background:var(--card)}

  .pattern{position:absolute;inset:0;
    background:linear-gradient(135deg,var(--card-back-light) 0%,var(--card-back-dark) 55%,var(--card-back) 100%)}

  .wordmark{position:absolute;display:flex;flex-direction:column;align-items:center;gap:12px;
    font-family:"Cinzel",serif;font-weight:600;color:var(--silver);letter-spacing:1.5px;
    line-height:1.3;text-align:center;white-space:nowrap}
  .wordmark__square{width:30px;height:30px;background:var(--gold);flex:none}
  .card--back .wordmark{left:50%;top:50%;transform:translate(-50%,-50%);font-size:19px}
  .card--front .wordmark{left:129px;top:72px;transform:translateX(-50%);font-size:15px;letter-spacing:1px}

  .divider{position:absolute;left:258px;top:40px;width:1px;height:170px;background:var(--rule)}

  .details{position:absolute;left:282px;top:40px;font-family:"Tinos",serif;color:var(--text)}
  .details__name{font-family:"Cinzel",serif;font-weight:500;font-size:17px;color:var(--gold);letter-spacing:1px}
  .details__role{font-size:12.5px;margin-top:2px}
  .contacts{list-style:none;margin-top:16px;font-size:12px;line-height:19px}
  .contacts li{display:flex;align-items:center;gap:8px}
  .contacts svg{width:11px;height:11px;flex:none}
  .address{margin-top:14px;font-size:12px;line-height:17px}

  .band{position:absolute;left:0;bottom:0;width:540px;height:90px}
</style>
</head>
<body>
<main class="stage">

  <section class="card card--back" aria-label="Card back">
    <div class="pattern" role="img" aria-label="Repeating tonal monogram pattern across the card back"></div>
    <div class="wordmark">
      <span class="wordmark__square"></span>
      <span>RENWICK TOLLIVER<br>CONSTRUCTION</span>
    </div>
  </section>

  <section class="card card--front" aria-label="Card front">
    <div class="wordmark">
      <span class="wordmark__square"></span>
      <span>RENWICK TOLLIVER<br>CONSTRUCTION</span>
    </div>

    <div class="divider"></div>

    <div class="details">
      <p class="details__name">LIONEL ASHBY</p>
      <p class="details__role">Managing Director</p>
      <ul class="contacts">
        <li><svg viewBox="0 0 12 12"><path fill="var(--gold)" d="M2.5 1l2 2-1 1.2a6 6 0 0 0 4.3 4.3L9 7.5l2 2-1.3 1.5C5.5 11 1 6.5 1 2.3z"/></svg>07822254961</li>
        <li><svg viewBox="0 0 12 12"><rect x="1" y="2.5" width="10" height="7" fill="var(--gold)"/><path d="M1 2.5l5 4 5-4" fill="none" stroke="var(--card)" stroke-width="1"/></svg>info@renwick-tolliver</li>
        <li><svg viewBox="0 0 12 12"><circle cx="6" cy="6" r="5" fill="none" stroke="var(--gold)" stroke-width="1.3"/><path d="M1 6h10M6 1c-2.5 3-2.5 7 0 10M6 1c2.5 3 2.5 7 0 10" fill="none" stroke="var(--gold)" stroke-width="0.9"/></svg>www.renwick-tolliver.co.uk</li>
      </ul>
      <p class="address">421, Address line goes here<br>45452, Country Name</p>
    </div>

    <svg class="band" viewBox="0 0 540 90" preserveAspectRatio="none" aria-hidden="true">
      <defs>
        <linearGradient id="goldBand" x1="0" y1="0" x2="1" y2="0">
          <stop offset="0" stop-color="var(--gold-dark)"/>
          <stop offset=".45" stop-color="var(--gold-light)"/>
          <stop offset="1" stop-color="var(--gold)"/>
        </linearGradient>
      </defs>
      <path d="M0 62 L540 14 L540 22 L0 70 Z" fill="var(--silver)"/>
      <path d="M0 74 L540 26 L540 90 L0 90 Z" fill="url(#goldBand)"/>
    </svg>
  </section>

</main>
</body>
</html>
```